Independent Financial Advisor Billboard Campaign - Maple Crest Financial

I am a local, independent financial advisor. My company is Maple Crest Financial, located in Charleston, WV. My main source of revenue comes from those nearing or entering retirement that need assistance with financial planning and investment management. Many are looking to rollover their employer retirement plan into an IRA account. I would like a billboard design campaign that focuses on this type of client. Please see our website www.maplecrestfinancial.com for more information.

```html
<!DOCTYPE html>
<html lang="en">
<head>
<meta charset="utf-8">
<title>Maple Crest Financial – Retirement Done Right Billboard</title>
<link href="https://fonts.googleapis.com/css2?family=Poppins:wght@600;700;800&display=swap" rel="stylesheet">
<style>
  :root {
    --page-bg: #cfcfcf;
    --board-white: #ffffff;
    --brand-blue: #15427c;
    --headline-gray: #5e5e5e;
    --pill-navy: #0c1b36;
    --text-white: #ffffff;
    --photo-light: #e8ecf2;
    --photo-mid: #c9d2de;
  }
  * { box-sizing: border-box; margin: 0; padding: 0; }
  html, body {
    width: 1066px;
    height: 1200px;
    overflow: hidden;
    background: var(--page-bg);
    font-family: "Poppins", sans-serif;
  }
  .stage {
    width: 1066px;
    height: 1200px;
    display: flex;
    align-items: center;
    justify-content: center;
  }
  .billboard {
    position: relative;
    width: 1000px;
    height: 327px;
    background: var(--board-white);
    overflow: hidden;
    box-shadow: 8px 8px 10px rgba(0, 0, 0, 0.35);
  }
  .headline {
    position: absolute;
    left: 50px;
    top: 20px;
    font-weight: 800;
    font-size: 98px;
    line-height: 0.9;
    letter-spacing: -2px;
    text-transform: uppercase;
  }
  .headline-top { display: block; color: var(--brand-blue); }
  .headline-bottom { display: block; color: var(--headline-gray); }
  .advisor-photo {
    position: absolute;
    left: 770px;
    top: 9px;
    width: 227px;
    height: 223px;
    background: radial-gradient(ellipse at 50% 40%, var(--photo-light) 0%, var(--photo-mid) 100%);
  }
  .contact-band {
    position: absolute;
    left: 0;
    top: 232px;
    width: 1000px;
    height: 95px;
    background: var(--brand-blue);
  }
  .phone {
    position: absolute;
    left: 51px;
    top: 22px;
    color: var(--text-white);
    font-weight: 700;
    font-size: 38px;
    letter-spacing: 0.5px;
  }
  .brand-name {
    position: absolute;
    left: 352px;
    top: 34px;
    display: flex;
    align-items: center;
    gap: 8px;
    color: var(--text-white);
    font-weight: 600;
    font-size: 16px;
    white-space: nowrap;
  }
  .brand-mark {
    width: 20px;
    height: 20px;
    background: var(--text-white);
  }
  .web-pill {
    position: absolute;
    left: 575px;
    top: 22px;
    width: 425px;
    height: 47px;
    background: var(--pill-navy);
    border-radius: 24px 0 0 24px;
    display: flex;
    align-items: center;
    justify-content: center;
    color: var(--text-white);
    font-weight: 700;
    font-size: 17px;
    letter-spacing: 1.2px;
  }
</style>
</head>
<body>
  <main class="stage">
    <section class="billboard">
      <h1 class="headline">
        <span class="headline-top">Retirement</span>
        <span class="headline-bottom">Done Right!</span>
      </h1>
      <div class="advisor-photo" role="img" aria-label="Portrait photo of the financial advisor in a white polo shirt"></div>
      <div class="contact-band">
        <div class="phone">304.555.0182</div>
        <div class="brand-name"><span class="brand-mark"></span>Maple Crest Financial</div>
        <div class="web-pill">www.maplecrestfinancial.com</div>
      </div>
    </section>
  </main>
</body>
</html>
```